Business Card Design for Marketing Firm

Looking for business card design for higher end marketing firm. Clean but impressionable/trendy. We are a marketing firm that represents manufacturers in the foodservice equipment and supply industry. Our customers are end users such has hotels, restaurants, country clubs, convention centers and casinos as well as distributors of restaurants supplies and equipment, and manufacturers of foodservice equipment and supplies.
Target Market(s)
Hotels, Restaurants, Supply & Equipment Distributors, Foodservice Manufacturers
Industry/Entity Type
Foodservice/Hospitality
Contact Information for Business Card
Name, Title, Contact Number, Email, Website, Social Media, Address
Requirements
Must have
- Clean & Simple but Serious and Impressionable

```html
<!DOCTYPE html>
<html lang="en">
<head>
<meta charset="utf-8">
<title>Harbor Table Reps – Business Card</title>
<link href="https://fonts.googleapis.com/css2?family=Crimson+Text:wght@400;600&display=swap" rel="stylesheet">
<style>
  :root {
    --navy: #000080;
    --white: #ffffff;
    --backdrop: #8f8f8f;
  }
  * { margin: 0; padding: 0; box-sizing: border-box; }
  html, body {
    width: 1200px; height: 1200px; overflow: hidden;
    background: var(--backdrop);
    font-family: "Crimson Text", Georgia, serif;
  }
  .card {
    position: absolute; left: 250px; width: 700px; height: 400px;
    border-radius: 22px; overflow: hidden;
    box-shadow: 0 3px 8px rgba(0,0,0,0.25);
  }
  .card-front { top: 170px; background: var(--navy); color: var(--white); }
  .card-back { top: 631px; background: var(--white); color: var(--navy); }

  .contact-block { position: absolute; left: 39px; top: 130px; }
  .person-name { font-size: 32px; font-weight: 600; letter-spacing: 1.5px; line-height: 1; }
  .person-title { font-size: 20px; margin-top: 6px; letter-spacing: 0.5px; }
  .address { margin-top: 16px; font-size: 17.5px; line-height: 24px; }
  .channels { margin-top: 14px; list-style: none; font-size: 17.5px; }
  .channels li { display: flex; align-items: center; height: 25px; }
  .channels li:first-child { font-size: 19.5px; height: 27px; }
  .channels svg { width: 14px; height: 14px; margin-right: 10px; fill: var(--white); flex: none; }

  .front-brand {
    position: absolute; right: 40px; top: 50%; transform: translateY(-50%);
    text-align: right; font-size: 62px; font-weight: 600;
    letter-spacing: 2px; line-height: 1.02;
  }

  .brand-mark {
    position: absolute; left: 50%; top: 88px; width: 120px; height: 120px;
    margin-left: -60px; border-radius: 50%; background: var(--navy);
  }
  .brand-name {
    position: absolute; left: 0; right: 0; top: 244px;
    text-align: center; font-size: 42px; font-weight: 600;
    letter-spacing: 1px; line-height: 1;
  }
</style>
</head>
<body>
  <section class="card card-front">
    <div class="contact-block">
      <h1 class="person-name">DANA WHITFORD</h1>
      <p class="person-title">Founder &amp; CEO</p>
      <p class="address">Harbor Table Reps<br>4820 Linden Court<br>Fairview, CT 06999</p>
      <ul class="channels">
        <li>
          <svg viewBox="0 0 24 24" aria-hidden="true"><path d="M6.6 10.8a15 15 0 0 0 6.6 6.6l2.2-2.2a1 1 0 0 1 1-.25 11 11 0 0 0 3.6.6 1 1 0 0 1 1 1V20a1 1 0 0 1-1 1A17 17 0 0 1 3 4a1 1 0 0 1 1-1h3.5a1 1 0 0 1 1 1c0 1.25.2 2.45.6 3.6a1 1 0 0 1-.25 1z"/></svg>
          (555) 014-2276
        </li>
        <li>
          <svg viewBox="0 0 24 24" aria-hidden="true"><path d="M2 5h20v14H2V5zm2 2v.3l8 6.2 8-6.2V7H4z"/></svg>
          hello@harbortablereps.com
        </li>
        <li>
          <svg viewBox="0 0 24 24" aria-hidden="true"><circle cx="12" cy="12" r="10" fill="none" stroke="#fff" stroke-width="2.5"/><circle cx="12" cy="12" r="4"/></svg>
          harbortablereps.com
        </li>
      </ul>
    </div>
    <p class="front-brand">HARBOR<br>TABLE<br>REPS</p>
  </section>

  <section class="card card-back">
    <div class="brand-mark" aria-hidden="true"></div>
    <p class="brand-name">HARBOR TABLE REPS</p>
  </section>
</body>
</html>
```